Veltrano.co - Polar Expeditions Specialists

We need a modern, visually striking business card for Veltrano.co, a company specialized in selling expedition cruises to the most remote regions on Earth, with a focus on the Arctic and Antarctica. The design should instantly communicate that the cardholder is an expert in polar travel. Use clean, premium aesthetics with cool tones like icy blue and white, possibly incorporating polar imagery (ice, glaciers, penguins, etc.)

Attached the logo

Contact Information for Business Card

Feels high-end and trustworthy.. Visually memorable — encourages people to keep it

Colors
0054AA
0677BA
7BADD7
CADEEF
E8F1F8

Requirements
Must have
• ice, glaciers, penguins, montains
Nice to have
• modern, transparente,

```html
<!DOCTYPE html>
<html lang="en">
<head>
<meta charset="UTF-8">
<title>Veltrano.co – Business Card</title>
<link href="https://fonts.googleapis.com/css2?family=Poppins:wght@300;400;500;600;700&display=swap" rel="stylesheet">
<style>
  :root {
    --brand-blue: #2d77b8;
    --ink: #141414;
    --card: #ffffff;
    --backdrop: #e4e9ea;
  }
  * { margin: 0; padding: 0; box-sizing: border-box; }
  html, body {
    width: 1200px; height: 960px; overflow: hidden;
    background: var(--backdrop);
    font-family: 'Poppins', sans-serif;
  }
  .card {
    position: absolute;
    left: 250px; width: 701px; height: 400px;
    background: var(--card);
    border-bottom: 4px solid var(--brand-blue);
    overflow: hidden;
  }
  .card--front { top: 60px; }
  .card--back { top: 500px; }

  .brand-dot {
    position: absolute;
    border-radius: 50%;
    background: var(--brand-blue);
  }
  .brand-name {
    position: absolute;
    color: var(--brand-blue);
    font-weight: 700;
    line-height: 1;
    white-space: nowrap;
  }
  .brand-tagline {
    position: absolute;
    color: var(--brand-blue);
    font-weight: 600;
    line-height: 1;
    white-space: nowrap;
  }

  /* Front */
  .card--front .brand-dot { left: 92px; top: 140px; width: 110px; height: 110px; }
  .card--front .brand-name { left: 240px; top: 160px; font-size: 66px; letter-spacing: -0.5px; }
  .card--front .brand-tagline { left: 242px; top: 238px; font-size: 21px; }

  /* Back */
  .card--back .brand-dot { left: 125px; top: 104px; width: 84px; height: 84px; }
  .card--back .brand-name { left: 0; width: 334px; text-align: center; top: 222px; font-size: 46px; letter-spacing: -0.5px; }
  .card--back .brand-tagline { left: 0; width: 334px; text-align: center; top: 274px; font-size: 15px; }

  .divider {
    position: absolute;
    left: 350px; top: 76px; width: 2px; height: 248px;
    background: var(--brand-blue);
  }
  .contact { position: absolute; left: 404px; top: 86px; width: 280px; }
  .person-name {
    font-size: 30px; line-height: 1; color: var(--brand-blue);
    letter-spacing: 0.5px; white-space: nowrap;
  }
  .person-name .first { font-weight: 600; }
  .person-name .last { font-weight: 300; }
  .person-title {
    margin-top: 6px; font-size: 16px; font-weight: 500; color: var(--ink); letter-spacing: 0.4px;
  }
  .address {
    margin-top: 14px; font-size: 17px; line-height: 26px; color: var(--brand-blue);
    letter-spacing: 0.4px; white-space: nowrap;
  }
  .contact-list { margin-top: 14px; list-style: none; }
  .contact-list li {
    display: flex; align-items: center; gap: 11px;
    font-size: 18px; line-height: 26px; color: var(--ink); letter-spacing: 0.4px; white-space: nowrap;
  }
  .contact-list svg { width: 17px; height: 17px; flex: none; fill: var(--brand-blue); }
</style>
</head>
<body>
  <section class="card card--front">
    <span class="brand-dot" aria-hidden="true"></span>
    <span class="brand-name">Veltrano.co</span>
    <span class="brand-tagline">Polar Expeditions Specialists</span>
  </section>

  <section class="card card--back">
    <span class="brand-dot" aria-hidden="true"></span>
    <span class="brand-name">Veltrano.co</span>
    <span class="brand-tagline">Polar Expeditions Specialists</span>

    <span class="divider" aria-hidden="true"></span>

    <div class="contact">
      <h1 class="person-name"><span class="first">Marika</span> <span class="last">Tesarova</span></h1>
      <p class="person-title">Founder &amp; CEO</p>
      <p class="address">1840 Harborline Ave. Suite 310<br>Lakemont, TX 76540</p>
      <ul class="contact-list">
        <li>
          <svg viewBox="0 0 24 24" aria-hidden="true"><path d="M6.6 10.8a15.1 15.1 0 0 0 6.6 6.6l2.2-2.2a1 1 0 0 1 1-.25 11.4 11.4 0 0 0 3.6.57 1 1 0 0 1 1 1V20a1 1 0 0 1-1 1A17 17 0 0 1 3 4a1 1 0 0 1 1-1h3.5a1 1 0 0 1 1 1c0 1.25.2 2.45.57 3.57a1 1 0 0 1-.25 1z"/></svg>
          (555) 204-7731
        </li>
        <li>
          <svg viewBox="0 0 24 24" aria-hidden="true"><path d="M2 5h20v14H2z M4 7v.4l8 5.2 8-5.2V7l-8 5.2z" fill-rule="evenodd"/></svg>
          info@yourwebsite.com
        </li>
        <li>
          <svg viewBox="0 0 24 24" aria-hidden="true"><path d="M12 2a10 10 0 1 0 0 20 10 10 0 0 0 0-20zm6.9 6h-3a15.7 15.7 0 0 0-1.3-3.6A8 8 0 0 1 18.9 8zM12 4c.8 1.2 1.5 2.5 1.9 4h-3.8c.4-1.5 1.1-2.8 1.9-4zM4.3 14a8 8 0 0 1 0-4h3.4a16.5 16.5 0 0 0 0 4zm.8 2h3a15.7 15.7 0 0 0 1.3 3.6A8 8 0 0 1 5.1 16zm3-8h-3a8 8 0 0 1 4.3-3.6A15.7 15.7 0 0 0 8.1 8zM12 20c-.8-1.2-1.5-2.5-1.9-4h3.8c-.4 1.5-1.1 2.8-1.9 4zm2.3-6H9.7a14.7 14.7 0 0 1 0-4h4.6a14.7 14.7 0 0 1 0 4zm.3 5.6A15.7 15.7 0 0 0 15.9 16h3a8 8 0 0 1-4.3 3.6zm1.7-5.6a16.5 16.5 0 0 0 0-4h3.4a8 8 0 0 1 0 4z"/></svg>
          www.yourwebsite.com
        </li>
      </ul>
    </div>
  </section>
</body>
</html>
```